Vantiqo custom business card design

Need a authentic, innovative business card design for a new mobile app business. I am uploading a few screen images from our app for you to view. I would like app design theme to match business card design. I can also send logo images.

```html
<!DOCTYPE html>
<html lang="en">
<head>
<meta charset="utf-8">
<title>Vantiqo Business Card</title>
<link rel="stylesheet" href="https://fonts.googleapis.com/css2?family=Roboto:wght@400;500;700&display=swap">
<style>
  :root {
    --bg: #e4e4e4;
    --purple-top: #7a04a0;
    --purple-bottom: #62038a;
    --ink: #262626;
    --white: #ffffff;
    --back-top: #2c2c2c;
    --back-bottom: #1d1d1d;
  }
  * { margin: 0; padding: 0; box-sizing: border-box; }
  html, body {
    width: 1200px; height: 1200px; overflow: hidden;
    background: var(--bg);
    font-family: "Roboto", Arial, sans-serif;
  }
  .card {
    position: absolute;
    left: 257px;
    width: 686px;
    height: 392px;
    overflow: hidden;
  }
  .card--front { top: 165px; background: linear-gradient(180deg, var(--purple-top), var(--purple-bottom)); }
  .card--back { top: 653px; background: linear-gradient(180deg, var(--back-top), var(--back-bottom)); }
  .card__shape { position: absolute; inset: 0; width: 686px; height: 392px; }

  .contact { position: absolute; left: 42px; top: 76px; color: var(--white); }
  .contact__name { font-size: 26px; font-weight: 700; line-height: 1; letter-spacing: 0.2px; }
  .contact__role { font-size: 16.5px; font-weight: 500; margin-top: 4px; }
  .contact__address { font-size: 16.5px; line-height: 21px; margin-top: 23px; }
  .contact__list { list-style: none; margin-top: 15px; }
  .contact__item {
    display: flex; align-items: center; gap: 9px;
    font-size: 16.5px; height: 22px;
  }
  .contact__icon { width: 17px; height: 15px; flex: none; fill: var(--white); }

  .brand {
    position: absolute; left: 430px; top: 168px;
    display: flex; align-items: center; gap: 12px;
  }
  .brand__dot { width: 24px; height: 24px; border-radius: 50%; background: var(--purple-top); }
  .brand__name { font-size: 44px; font-weight: 700; color: var(--ink); line-height: 1; }

  .back-brand {
    position: absolute; left: 0; right: 0; top: 158px;
    display: flex; justify-content: center; align-items: center; gap: 16px;
  }
  .back-brand__dot { width: 34px; height: 34px; border-radius: 50%; background: var(--white); }
  .back-brand__name { font-size: 62px; font-weight: 700; color: var(--white); line-height: 1; }
  .back-url {
    position: absolute; left: 0; right: 0; top: 334px;
    text-align: center; color: var(--white);
    font-size: 16px; letter-spacing: 10px; padding-left: 10px;
  }
</style>
</head>
<body>

<section class="card card--front">
  <svg class="card__shape" viewBox="0 0 800 457" preserveAspectRatio="none" aria-hidden="true">
    <rect x="577" y="0" width="223" height="457" fill="var(--white)"/>
    <circle cx="577" cy="227" r="255" fill="var(--white)"/>
    <path d="M 454 0 A 258 258 0 0 0 460 457" fill="none" stroke="var(--ink)" stroke-width="5"/>
    <circle cx="422" cy="32" r="14" fill="var(--ink)" stroke="var(--white)" stroke-width="2"/>
  </svg>

  <div class="contact">
    <div class="contact__name">DANIEL HART</div>
    <div class="contact__role">CEO/FOUNDER</div>
    <div class="contact__address">2140 Willowmere Road<br>Juneau, Alaska 34821</div>
    <ul class="contact__list">
      <li class="contact__item">
        <svg class="contact__icon" viewBox="0 0 16 16"><path d="M3.5 1l2.5 3-1.5 2c1 2 3 4 5 5l2-1.5 3 2.5-1.5 2.5C7 14 2 9 1 2.5z"/></svg>
        614 205 7391
      </li>
      <li class="contact__item">
        <svg class="contact__icon" viewBox="0 0 16 16"><path d="M4 0h8v16H4zM5.5 1.5v11h5v-11zM7 13.5h2v1H7z" fill-rule="evenodd"/></svg>
        742 318 5026
      </li>
      <li class="contact__item">
        <svg class="contact__icon" viewBox="0 0 16 16"><path d="M4 1h8v5H4zM1 7h14v6H1zM4 14h8v1H4z"/></svg>
        529 473 1186
      </li>
      <li class="contact__item">
        <svg class="contact__icon" viewBox="0 0 16 16"><path d="M1 4h14v9H1zM2 5l6 4.5L14 5" fill-rule="evenodd"/><path d="M2 5l6 4.5L14 5" fill="none" stroke="var(--purple-top)" stroke-width="1.2"/></svg>
        daniel@vantiqo.com
      </li>
      <li class="contact__item">
        <svg class="contact__icon" viewBox="0 0 16 16"><circle cx="8" cy="8" r="7"/><path d="M4 5c2 0 2 2 3 3s-1 3 0 4M10 3c0 2 2 2 3 3M9 9c1 0 2 1 2 3" fill="none" stroke="var(--purple-top)" stroke-width="1.3"/></svg>
        www.vantiqo.com
      </li>
    </ul>
  </div>

  <div class="brand">
    <span class="brand__dot"></span>
    <span class="brand__name">Vantiqo</span>
  </div>
</section>

<section class="card card--back">
  <div class="back-brand">
    <span class="back-brand__dot"></span>
    <span class="back-brand__name">Vantiqo</span>
  </div>
  <div class="back-url">www.vantiqo.com</div>
</section>

</body>
</html>
```